Cafe menu flyer design

I need if possible A4 double sided menus. Two exemplars: first will contain breakfast menu on one side & refreshments menu on the other side, second exemplar will contain lunch menu on one side & refreshments menu on the other side. We do not need a description of the cafe or any history on these flyers, but design should reflect our surroundings and activities this area. We are located in main ski resort in UK-Cairngorm Mountains, right on the main ski road. The slopes are only 2 miles away from us. We are also very popular with wild life enthusiasts. Continues in design brief!

Cafe

```html
<!DOCTYPE html>
<html lang="en">
<head>
<meta charset="utf-8">
<title>Fiona's @ Birchwood Cafe – Breakfast Menu</title>
<link href="https://fonts.googleapis.com/css2?family=Jost:ital,wght@0,500;0,600;1,500&display=swap" rel="stylesheet">
<style>
  :root {
    --sky: #8fcbea;
    --mountain: #8a7796;
    --grass: #7aab1e;
    --night: #1d1c3b;
    --ink: #111111;
    --text: #ffffff;
    --robin: #d8232a;
    --badge: #3f5f9e;
  }
  html, body { margin: 0; padding: 0; overflow: hidden; }
  body { width: 1200px; height: 927px; background: var(--night); }
  .menu {
    position: relative; width: 1200px; height: 927px; overflow: hidden;
    background: var(--night); color: var(--text);
    font-family: "Jost", "Futura", sans-serif; font-weight: 500;
  }
  .landscape {
    position: absolute; left: 0; top: 0; width: 1200px; height: 250px;
    background: linear-gradient(180deg, var(--sky) 0%, var(--sky) 18%, var(--mountain) 45%, var(--mountain) 100%);
  }
  .treeline {
    position: absolute; left: 0; top: 230px; width: 1200px; height: 60px;
    background: var(--grass);
    border-radius: 0 0 24px 24px;
  }
  .skier {
    position: absolute; left: 26px; top: 10px; width: 78px; height: 90px;
    background: linear-gradient(160deg, var(--robin), #2aa0c8);
    border-radius: 8px;
  }
  .brand {
    position: absolute; left: 80px; top: 98px; margin: 0;
    font-family: "Jost", "Futura", sans-serif; font-weight: 600;
    font-size: 72px; line-height: 1; color: var(--ink); white-space: nowrap;
  }
  .address {
    position: absolute; right: 172px; top: 174px; margin: 0;
    font-size: 17px; font-weight: 600; color: var(--ink);
  }
  .section-title {
    position: absolute; left: 55px; top: 318px; margin: 0;
    font-size: 25px; font-weight: 600; letter-spacing: 0.5px;
  }
  .items { position: absolute; top: 360px; margin: 0; padding: 0; list-style: none; font-size: 20px; line-height: 27.2px; }
  .items li { position: relative; white-space: nowrap; }
  .items .price { position: absolute; top: 0; }
  .items .desc { font-style: italic; }
  .items-left { left: 70px; width: 520px; }
  .items-left .price { left: 402px; }
  .items-right { left: 610px; width: 520px; }
  .items-right .price { left: 400px; }
  .note-caps { text-transform: uppercase; }
  .robin {
    position: absolute; left: 39px; top: 763px; width: 130px; height: 164px;
    background: var(--robin); border-radius: 50% 10% 0 0;
  }
  .info {
    position: absolute; left: 270px; top: 770px; margin: 0;
    font-size: 19px; line-height: 27.4px;
  }
  .social-square {
    position: absolute; left: 731px; top: 763px; width: 105px; height: 105px;
    background: var(--badge); border-radius: 14px;
  }
  .social {
    position: absolute; left: 850px; top: 760px; width: 280px; margin: 0;
    text-align: center; font-size: 19px; line-height: 27.4px; font-weight: 600;
  }
</style>
</head>
<body>
<main class="menu">
  <div class="landscape" role="img" aria-label="Snow-capped mountain range under a blue sky with white clouds"></div>
  <div class="treeline" role="img" aria-label="Green forest treeline along the foot of the mountains"></div>
  <div class="skier" role="img" aria-label="Small illustration of a skier descending the slope"></div>

  <h1 class="brand">Fiona's @ Birchwood Cafe</h1>
  <p class="address">Birchwood, Strathmore, PH99 4XB. Tel:01234567890</p>

  <h2 class="section-title">BREAKFAST 9AM - 12NOON</h2>

  <ul class="items items-left">
    <li>Small breakfast<span class="price">£5.50</span></li>
    <li class="desc">bacon, egg, sausage</li>
    <li>Large breakfast<span class="price">£7.95</span></li>
    <li class="desc">bacon, egg, sausage, black pudding,</li>
    <li class="desc">potato scone, beans, tomato</li>
    <li class="note-caps">Both breakfasts include tea/coffee/plain</li>
    <li class="note-caps">hot chocolate &amp; one slice of toast.</li>
    <li class="note-caps">One free refill drink.</li>
    <li>Pancake breakfast.<span class="price">£4.95</span></li>
    <li class="desc">Three pancakes served with hot forest berry</li>
    <li class="desc">sauce and maple syrup</li>
    <li>Add three rushers of bacon<span class="price">£6.95</span></li>
  </ul>

  <ul class="items items-right">
    <li>Round of toast<span class="price">£2.00</span></li>
    <li class="desc">served with butter and jam</li>
    <li>Beans on toast<span class="price">£3.50</span></li>
    <li>Beans &amp; egg on toast<span class="price">£4.00</span></li>
    <li>Beans &amp; bacon on toast<span class="price">£4.50</span></li>
    <li>Bacon roll<span class="price">£2.90</span></li>
    <li>Lorne roll<span class="price">£2.50</span></li>
    <li>Black pudding roll<span class="price">£2.50</span></li>
    <li>Fried egg roll<span class="price">£2.00</span></li>
    <li>2 item roll<span class="price">£4.00</span></li>
    <li>Rolls with assorted cold fillings<span class="price">£2.20-£3.20</span></li>
    <li>Pies assorted<span class="price">£2.50</span></li>
  </ul>

  <div class="robin" role="img" aria-label="Red stylised bird standing on thin legs"></div>

  <p class="info">Gluten free bread, cakes and veggie<br>breakfast available - ask staff!<br>At the hight of the season evening meals<br>available. Ask staff for more info!</p>

  <div class="social-square"></div>
  <p class="social">Like us on Gatherly!<br>gatherly.example/pages/<br>Fionas-at-Birchwood-<br>Cafe/100200300400500</p>
</main>
</body>
</html>
```